Creative, fresh business card design for Ripplecraft Facades

We need a fresh, creative business card design for Ripplecraft Facades. We are the manufacturer of Ripplecraft Facades in Australia. Wall panels are 2400 x 1200mm panels made from MDF and feature 3D patterns on the face of the panel. The colours to be used are green, silver/grey and white RGB
Red 187
Green 207
Blue 65.

An idea is to possibly use a watermark of one of our designs as a background (like on the "Grids" design on the left hand side of page 2 of our brochure).

Target Market(s)

Interior designers, architects, builders and home renovators

Industry/Entity Type

Business

Contact Information for Business Card

Details to go on the card are:
Our logo (attached),
Slogan: "Decorative panels for interiors and exteriors",
Contact name,
Position,
Mobile phone number,
Business address,
Business phone,
Business fax,
Website and
Email address.

I have attached a few images of our panels and our brochure for reference.

The colours of the business card should feature our logo colours which are: RGB
Red 187
Green 207
Blue 65

Requirements
Must have
• Very modern fonts and design. Some of the designs shown especially the "Prisms" design which is a popular design.
Nice to have
• Creative but simple design. Very contemporary.
Should not have
• Anything ornate or old fashioned.

```html
<!DOCTYPE html>
<html lang="en">
<head>
<meta charset="utf-8">
<title>Ripplecraft Facades — Business Card</title>
<link rel="stylesheet" href="https://fonts.googleapis.com/css2?family=Arimo:wght@400;700&display=swap">
<style>
  :root {
    --brand-green: rgb(187, 207, 65);
    --silver: #8e8f91;
    --silver-light: #a9aaac;
    --ink: #3d3d3f;
    --card-white: #f6f5f2;
    --ripple-shade: #e4e3df;
    --rule: #9aa0a8;
    --backdrop: #ecebe8;
  }
  * { box-sizing: border-box; margin: 0; padding: 0; }
  html, body {
    width: 1200px; height: 987px; overflow: hidden;
    background: var(--backdrop);
    font-family: "Arimo", Arial, sans-serif;
    color: var(--ink);
  }
  .canvas { position: relative; width: 1200px; height: 987px; }
  .card {
    position: absolute; left: 292px; width: 615px; height: 349px;
    overflow: hidden;
    box-shadow: 0 2px 6px rgba(0,0,0,0.18);
  }
  .card--front { top: 130px; }
  .card--back { top: 505px; height: 351px; }
  .ripple-texture {
    position: absolute; inset: 0;
    background:
      radial-gradient(circle at 30% 35%, var(--card-white) 0%, var(--ripple-shade) 100%);
  }
  .brand { position: absolute; display: flex; align-items: center; gap: 10px; }
  .brand__square { background: var(--brand-green); flex: none; }
  .brand__name { color: var(--brand-green); font-weight: 700; white-space: nowrap; }
  .slogan {
    position: absolute; color: var(--silver-light);
    font-size: 12.5px; letter-spacing: 2.6px; line-height: 15px;
    white-space: nowrap;
  }
  .card--front .brand { right: 32px; top: 86px; }
  .card--front .brand__square { width: 40px; height: 40px; }
  .card--front .brand__name { font-size: 25px; }
  .card--front .slogan { right: 32px; top: 160px; }

  .name-tab {
    position: absolute; left: 0; top: 188px; width: 11px; height: 44px;
    background: var(--silver-light);
  }
  .person { position: absolute; left: 32px; top: 188px; }
  .person__name { color: var(--brand-green); font-weight: 700; font-size: 22px; letter-spacing: 0.3px; }
  .person__role { color: var(--silver); font-size: 16px; margin-top: 3px; }
  .divider {
    position: absolute; left: 32px; right: 32px; top: 242px;
    height: 1px; background: var(--rule);
  }
  .contacts { position: absolute; left: 32px; top: 254px; list-style: none; }
  .contacts li { display: flex; align-items: center; gap: 9px; font-size: 16.5px; height: 23px; }
  .contacts svg { width: 15px; height: 15px; fill: var(--brand-green); flex: none; }
  .address {
    position: absolute; right: 32px; top: 254px; text-align: right;
    font-size: 16.5px; line-height: 23px; font-style: normal;
  }
  .address .web { letter-spacing: 1px; }
  .edge-band { position: absolute; left: 0; right: 0; bottom: 0; }
  .edge-band__silver { height: 2px; background: var(--silver-light); }
  .edge-band__green { height: 6px; background: var(--brand-green); }

  .card--back .brand-stack {
    position: absolute; left: 0; right: 0; top: 140px;
    display: flex; flex-direction: column; align-items: center;
  }
  .card--back .brand { position: static; }
  .card--back .brand__square { width: 46px; height: 46px; }
  .card--back .brand__name { font-size: 31px; }
  .card--back .slogan { position: static; margin-top: 44px; }
</style>
</head>
<body>
<main class="canvas">
  <section class="card card--front">
    <div class="ripple-texture" role="img" aria-label="Embossed ripple panel texture"></div>

    <div class="brand">
      <span class="brand__square"></span>
      <span class="brand__name">Ripplecraft Facades</span>
    </div>
    <p class="slogan">sculpted wall panels<br>for homes &amp; workplaces</p>

    <span class="name-tab"></span>
    <div class="person">
      <h1 class="person__name">DANIEL HART</h1>
      <p class="person__role">CEO&amp;Founder</p>
    </div>
    <div class="divider"></div>

    <ul class="contacts">
      <li>
        <svg viewBox="0 0 16 16"><path d="M3.6 1.2l2.3 2.6-1.4 2c.9 2 2.4 3.6 4.4 4.6l1.9-1.5 2.8 2.2-1.2 2.4C7.4 13.3 2.6 8.6 1.2 3z"/></svg>
        (555) 214-7730
      </li>
      <li>
        <svg viewBox="0 0 16 16"><rect x="4" y="1" width="8" height="4"/><rect x="1" y="6" width="14" height="6" rx="1"/><rect x="4" y="10" width="8" height="5"/></svg>
        (555) 214-7731
      </li>
      <li>
        <svg viewBox="0 0 16 16"><path d="M1 3h14v10H1z M1 3l7 5.5L15 3" stroke="#f6f5f2" stroke-width="1.2"/></svg>
        dhart@ripplecraft.com
      </li>
    </ul>

    <address class="address">
      42 Harbour Crescent<br>
      Geelong, Victoria 3220<br>
      <span class="web">www.ripplecraft.com</span>
    </address>

    <div class="edge-band">
      <div class="edge-band__silver"></div>
      <div class="edge-band__green"></div>
    </div>
  </section>

  <section class="card card--back">
    <div class="ripple-texture" role="img" aria-label="Embossed ripple panel texture"></div>
    <div class="brand-stack">
      <div class="brand">
        <span class="brand__square"></span>
        <span class="brand__name">Ripplecraft Facades</span>
      </div>
      <p class="slogan">sculpted wall panels<br>for homes &amp; workplaces</p>
    </div>
  </section>
</main>
</body>
</html>
```